Lantern Petals Website v.1 - attract floral shop franchisees

I need a simple information website for my new business. We are a franchisor of flower shops. The overall purpose of the website is to promote the company and the service, especially to potential franchisees and retailers. Only about 4 pages are required including homepage, About, For Supermarkets, For Franchisees, and Contact. No special functions are required except the site will have two separate inquiry forms that must be filled out online and submitted via automated email. Similarly, an email form should be linked from the Contact page. I have a logo and business cards designed by ArtMingle, and I would like the site to have a consistent color scheme and style. The key to design will be to express the joy and love associated with flowers and floral bouquets.
IMPORTANT - I will be exporting the website design to Wordpress CMS in a site hosted by HostNimbus. For smooth integration into WordPress hosted by HostNimbus, the designer should build the site using a WordPress-friendly format. Ideally, they should use HTML, CSS, and PHP. Creating a custom theme or using a page builder that exports to WordPress-compatible files is best. This ensures the site can be easily imported and managed within WordPress.

Target Market(s)

Potential franchisees (existing florists or creative types who might like to own a floral business) and supermarkets who might want us to run their floral department

Industry/Entity Type

Floral retailing

Requirements
Must have
• A brand theme that is beautiful, consistent throughout and builds on the logo design
Nice to have
• Show gender and ethnic diversity in customers and florists. Pictures of happy florists (for franchisees) and pictures of amazing floral department displays (for supermarkets)

```html
<!DOCTYPE html>
<html lang="en">
<head>
<meta charset="utf-8">
<title>Lantern Petals</title>
<link href="https://fonts.googleapis.com/css2?family=Poppins:wght@400;500;600;700;800&family=Lato:wght@400;700&family=Allura&display=swap" rel="stylesheet">
<style>
:root{
  --green:#10954a;
  --green-dark:#0b7a3b;
  --orange:#f0ae2e;
  --text:#333333;
  --muted:#555555;
  --white:#ffffff;
  --soft:#efefee;
  --footer:#2b2b2b;
  --footer-line:#444444;
}
*{box-sizing:border-box;margin:0;padding:0}
html,body{width:1200px;height:3501px;overflow:hidden}
body{position:relative;font-family:"Lato",sans-serif;color:var(--text);background:var(--white)}
.abs{position:absolute}
.script{font-family:"Allura",cursive;font-weight:400}
.btn{position:absolute;display:flex;align-items:center;justify-content:center;font-family:"Poppins",sans-serif;font-weight:600;font-size:15px;color:var(--white);background:var(--orange);border-radius:8px;border-bottom:3px solid var(--green);border-left:2px solid var(--green);text-transform:uppercase}
.btn.green{background:var(--green);border-color:var(--orange)}
/* header */
.site-header{position:absolute;left:0;top:0;width:1200px;height:98px;background:var(--white)}
.brand{position:absolute;display:flex;align-items:center;gap:10px;font-family:"Poppins",sans-serif;font-weight:600;color:var(--orange);white-space:nowrap}
.brand .dot{width:22px;height:22px;border-radius:50%;background:var(--green)}
.nav a{position:absolute;top:38px;font-family:"Poppins",sans-serif;font-size:14px;color:#333;text-decoration:none;white-space:nowrap}
.nav a.active{color:var(--orange)}
/* hero */
.hero{position:absolute;left:0;top:98px;width:1200px;height:800px;overflow:hidden}
.hero-photo{position:absolute;inset:0;background:
  radial-gradient(ellipse 230px 380px at 78% 62%,rgba(244,241,234,.95),rgba(244,241,234,0) 100%),
  radial-gradient(ellipse 120px 120px at 74% 30%,rgba(196,150,110,.8),rgba(196,150,110,0) 100%),
  linear-gradient(180deg,#4a4d3e 0%,#6f7261 18%,#a6a393 40%,#bdb8aa 70%,#cfcabd 100%)}
.hero-copy{position:absolute;left:110px;top:150px;color:var(--white)}
.hero-copy .welcome{font-size:68px;line-height:1}
.hero-copy h1{font-family:"Poppins",sans-serif;font-weight:800;font-size:70px;line-height:1;margin-top:18px;letter-spacing:.5px;white-space:nowrap}
.hero-copy p{font-size:15.5px;line-height:23px;width:520px;margin-top:22px;padding-left:4px}
.dots{position:absolute;left:576px;top:697px;display:flex;gap:8px;align-items:center}
.dots span{width:10px;height:10px;border-radius:50%;background:var(--white)}
.dots span.on{width:14px;height:14px;background:var(--green);border:2px solid var(--white)}
.hero-wave{position:absolute;left:0;top:570px}
/* section headings */
.sec-title{position:absolute;display:flex;align-items:center;gap:14px;font-family:"Poppins",sans-serif;font-weight:600;font-size:30px;color:var(--green);text-transform:uppercase;white-space:nowrap}
.sec-title .script{font-size:48px;color:var(--green);text-transform:none;line-height:1}
.sec-title.light,.sec-title.light .script{color:var(--white)}
.flower-icon{width:32px;height:32px}
.body-text{position:absolute;font-size:15px;line-height:26px;text-align:justify;color:var(--text)}
/* about */
.about-ornament{position:absolute;left:0;top:930px;width:140px;height:360px}
.about-hexes{position:absolute;left:0;top:900px;width:600px;height:520px}
/* supermarkets */
.supermarkets{position:absolute;left:0;top:1474px;width:1200px;height:457px;background:linear-gradient(180deg,#17a050 0%,#109348 60%,#0f8d45 100%)}
.supermarkets p{position:absolute;left:165px;top:180px;width:870px;font-size:15px;line-height:23px;text-align:center;color:var(--white)}
/* franchisees */
.fr-frame{position:absolute;left:604px;top:2056px;width:487px;height:357px;background:var(--green)}
.fr-photo{position:absolute;left:596px;top:2048px;width:487px;height:357px;background:
  radial-gradient(ellipse 110px 90px at 30% 55%,rgba(230,214,196,.9),rgba(230,214,196,0)),
  radial-gradient(ellipse 120px 100px at 70% 45%,rgba(238,200,170,.85),rgba(238,200,170,0)),
  radial-gradient(ellipse 90px 80px at 82% 78%,rgba(84,120,60,.8),rgba(84,120,60,0)),
  linear-gradient(120deg,#b9a78e,#8fa179 45%,#d9ccb8)}
/* contact */
.contact{position:absolute;left:0;top:2487px;width:1200px;height:656px;overflow:hidden}
.contact-bg{position:absolute;left:0;top:180px;width:1200px;height:476px;background:
  radial-gradient(ellipse 260px 120px at 35% 85%,rgba(230,190,200,.55),rgba(230,190,200,0)),
  radial-gradient(ellipse 200px 110px at 75% 80%,rgba(240,215,170,.5),rgba(240,215,170,0)),
  linear-gradient(180deg,#f1f1ef,#ece6e2 60%,#efe9e3)}
.contact p{position:absolute;left:270px;top:433px;width:660px;font-size:15px;line-height:24px;text-align:center;color:var(--muted)}
/* footer */
.site-footer{position:absolute;left:0;top:3143px;width:1200px;height:358px;background:var(--footer);color:var(--white)}
.site-footer h4{position:absolute;font-family:"Poppins",sans-serif;font-weight:600;font-size:19px}
.links{position:absolute;list-style:none;font-size:15px}
.links li{height:25.7px;display:flex;align-items:center;gap:10px}
.links li::before{content:"»";font-size:17px}
.social{position:absolute;left:112px;top:3350px;display:flex;gap:7px}
.social span{width:36px;height:36px;border-radius:50%;background:var(--white);border:2px solid var(--orange)}
.social span:first-child{background:var(--orange)}
.contact-list{position:absolute;left:864px;top:3250px;font-size:15px;line-height:26px}
.contact-list div{display:flex;gap:10px;margin-bottom:14px}
.contact-list svg{flex:none;margin-top:5px}
.copyright{position:absolute;left:0;top:302px;width:1200px;text-align:center;font-size:15px;color:var(--white)}
</style>
</head>
<body>

<header class="site-header">
  <div class="brand" style="left:112px;top:30px;font-size:26px"><span class="dot"></span>Lantern Petals</div>
  <nav class="nav">
    <a class="active" style="left:350px">Home</a>
    <a style="left:423px">About</a>
    <a style="left:497px">For Supermarkets</a>
    <a style="left:651px">For Franchisees</a>
    <a style="left:792px">Contact</a>
  </nav>
  <svg class="abs" style="left:898px;top:38px" width="20" height="20" viewBox="0 0 20 20"><circle cx="8" cy="8" r="6" fill="none" stroke="var(--green)" stroke-width="3"/><line x1="12.5" y1="12.5" x2="18" y2="18" stroke="var(--green)" stroke-width="3" stroke-linecap="round"/></svg>
  <svg class="abs" style="left:937px;top:38px" width="18" height="18" viewBox="0 0 18 18"><circle cx="9" cy="5" r="4.5" fill="var(--green)"/><path d="M1 18c0-6 4-8 8-8s8 2 8 8z" fill="var(--green)"/></svg>
  <div class="btn" style="left:985px;top:25px;width:106px;height:44px">Log In</div>
</header>

<section class="hero">
  <div class="hero-photo" role="img" aria-label="Smiling woman in a white dress and straw hat holding a bouquet of daisies in a flower field"></div>
  <div class="hero-copy">
    <div class="script welcome">Welcome to</div>
    <h1>LANTERN PETALS</h1>
    <p>Lorem ipsum dolor sit amet, consectetur adipiscing elit, sed do eiusmod tempor incididunt ut labore et dolore magna aliqua.</p>
  </div>
  <div class="btn" style="left:112px;top:387px;width:140px;height:42px">Get Started</div>
</section>
<svg class="hero-wave" width="1200" height="332" viewBox="0 570 1200 332">
  <path d="M0,584 C200,560 380,640 560,705 C760,775 950,860 1200,876 L1200,902 L0,902Z" fill="var(--orange)"/>
  <path d="M0,726 C250,692 480,742 700,802 C900,857 1050,888 1200,886 L1200,902 L0,902Z" fill="var(--white)"/>
  <path d="M0,738 C220,705 440,728 690,790 C470,760 250,770 0,832Z" fill="var(--green)"/>
</svg>
<div class="dots"><span></span><span class="on"></span><span></span></div>

<section class="about">
  <div class="about-ornament" role="img" aria-label="Bee illustration with dashed flight trail" style="background:radial-gradient(circle at 50% 15%,rgba(16,149,74,.3),rgba(16,149,74,0) 45%),radial-gradient(circle at 40% 62%,rgba(16,149,74,.15),rgba(16,149,74,0) 40%)"></div>
  <svg class="about-hexes" viewBox="0 0 600 520" role="img" aria-label="Hexagon collage of smiling florists in flower shops">
    <defs>
      <linearGradient id="hexA" x1="0" y1="0" x2="1" y2="1"><stop offset="0" stop-color="#4f5b45"/><stop offset="1" stop-color="#8d987a"/></linearGradient>
      <linearGradient id="hexB" x1="0" y1="0" x2="1" y2="1"><stop offset="0" stop-color="#c9c39d"/><stop offset="1" stop-color="#7f8b55"/></linearGradient>
      <linearGradient id="hexC" x1="0" y1="0" x2="1" y2="1"><stop offset="0" stop-color="#dfe3d8"/><stop offset="1" stop-color="#8a9a6e"/></linearGradient>
      <linearGradient id="hexD" x1="0" y1="0" x2="1" y2="1"><stop offset="0" stop-color="#7a4a3a"/><stop offset="1" stop-color="#c0392b"/></linearGradient>
      <linearGradient id="hexE" x1="0" y1="0" x2="1" y2="1"><stop offset="0" stop-color="#5d6a48"/><stop offset="1" stop-color="#d9648a"/></linearGradient>
      <linearGradient id="hexF" x1="0" y1="0" x2="1" y2="1"><stop offset="0" stop-color="#8b6a4a"/><stop offset="1" stop-color="#e0883a"/></linearGradient>
    </defs>
    <polygon points="152,153 193,82 275,82 316,153 275,224 193,224" fill="url(#hexA)"/>
    <polygon points="303,99 344,28 426,28 467,99 426,170 344,170" fill="url(#hexB)"/>
    <polygon points="421,201 462,130 544,130 585,201 544,272 462,272" fill="url(#hexC)"/>
    <polygon points="125,304 166,233 248,233 289,304 248,375 166,375" fill="url(#hexD)"/>
    <polygon points="244,405 285,334 367,334 408,405 367,476 285,476" fill="url(#hexE)"/>
    <polygon points="394,353 435,282 517,282 558,353 517,424 435,424" fill="url(#hexF)"/>
  </svg>
  <div class="sec-title" style="left:652px;top:985px">
    <svg class="flower-icon" viewBox="0 0 32 32"><g fill="var(--orange)"><circle cx="16" cy="6" r="5.5"/><circle cx="16" cy="26" r="5.5"/><circle cx="6" cy="16" r="5.5"/><circle cx="26" cy="16" r="5.5"/><circle cx="9" cy="9" r="4.5"/><circle cx="23" cy="23" r="4.5"/><circle cx="23" cy="9" r="4.5"/><circle cx="9" cy="23" r="4.5"/></g><circle cx="16" cy="16" r="4" fill="var(--white)"/></svg>
    <span class="script">About</span><span>Lantern Petals</span>
  </div>
  <p class="body-text" style="left:652px;top:1061px;width:438px">Fresh flowers convey beauty and love, and in our view should become something every person regularly enjoys. Lantern Petals is an entrepreneurial company created to make top quality fresh flowers and professionally-designed bouquets accessible to every consumer at affordable prices. Professional florists typically sell the finest quality stems, design the most beautiful bouquets and provide the finest customer service, but their costs – of floral products, retail spaces, labor and marketing – force them to pass high prices along to customers.</p>
  <div class="btn" style="left:652px;top:1320px;width:129px;height:42px">Learn More</div>
</section>

<section class="supermarkets">
  <div role="img" aria-label="Woman smelling flowers, softly tinted green" class="abs" style="left:0;top:0;width:1200px;height:457px;background:radial-gradient(ellipse 260px 200px at 62% 40%,rgba(255,255,255,.1),rgba(255,255,255,0)),radial-gradient(ellipse 200px 160px at 42% 75%,rgba(0,60,30,.12),rgba(0,60,30,0))"></div>
  <div class="sec-title light" style="left:423px;top:100px">
    <svg class="flower-icon" viewBox="0 0 32 32"><g fill="var(--orange)"><circle cx="16" cy="6" r="5.5"/><circle cx="16" cy="26" r="5.5"/><circle cx="6" cy="16" r="5.5"/><circle cx="26" cy="16" r="5.5"/><circle cx="9" cy="9" r="4.5"/><circle cx="23" cy="23" r="4.5"/><circle cx="23" cy="9" r="4.5"/><circle cx="9" cy="23" r="4.5"/></g><circle cx="16" cy="16" r="4" fill="var(--green)"/></svg>
    <span class="script">For</span><span>Supermarkets</span>
  </div>
  <p>Lantern Petals works with some of the country’s largest and most progressive supermarkets to provide franchisee ownership and operation of their strategically important floral departments. Supermarkets find that Lantern Petals is able to improve their financial outcomes, provide attentive customer service and satisfaction, and lift the quality of the entire store environment.</p>
  <div class="btn" style="left:537px;top:314px;width:126px;height:42px">Learn More</div>
</section>

<section class="franchisees">
  <div class="sec-title" style="left:110px;top:2056px">
    <svg class="flower-icon" viewBox="0 0 32 32"><g fill="var(--orange)"><circle cx="16" cy="6" r="5.5"/><circle cx="16" cy="26" r="5.5"/><circle cx="6" cy="16" r="5.5"/><circle cx="26" cy="16" r="5.5"/><circle cx="9" cy="9" r="4.5"/><circle cx="23" cy="23" r="4.5"/><circle cx="23" cy="9" r="4.5"/><circle cx="9" cy="23" r="4.5"/></g><circle cx="16" cy="16" r="4" fill="var(--white)"/></svg>
    <span class="script">For</span><span>Franchisees</span>
  </div>
  <p class="body-text" style="left:110px;top:2130px;width:435px;line-height:23px">Lantern Petals brings the best of professional florists and supermarkets together for the benefit of consumers. It supports a national network of owner-operator franchisees, who in many cases are multi-site professional florists, with comprehensive services to enhance franchise profitability. Lantern Petals works with some of the country’s largest and most progressive supermarkets to provide franchisee ownership and operation of their strategically important floral departments</p>
  <div class="btn" style="left:108px;top:2370px;width:130px;height:43px">Learn More</div>
  <div class="fr-frame"></div>
  <div class="fr-photo" role="img" aria-label="Two happy florists working at a laptop in a plant-filled shop"></div>
</section>

<section class="contact">
  <div class="contact-bg" role="img" aria-label="Faded photo of a florist among flower displays"></div>
  <div role="img" aria-label="Honeycomb, bee and flower illustration" class="abs" style="left:80px;top:0;width:280px;height:320px;background:radial-gradient(circle at 60% 30%,rgba(240,174,46,.25),rgba(240,174,46,0) 50%),radial-gradient(circle at 30% 60%,rgba(16,149,74,.12),rgba(16,149,74,0) 40%)"></div>
  <svg class="abs" style="left:0;top:0" width="1200" height="330" viewBox="0 0 1200 330">
    <path d="M0,300 C300,320 560,200 760,90 C900,20 1050,10 1200,8 L1200,320 L0,320Z" fill="var(--orange)"/>
    <path d="M0,320 C250,325 540,230 720,165 C850,120 990,112 1200,120 L1200,330 L0,330Z" fill="var(--soft)"/>
    <path d="M695,240 C820,195 950,170 1060,180 C1120,186 1170,200 1200,210 L1200,260 C1160,240 1100,230 1040,232 C920,236 820,242 695,240Z" fill="var(--green)"/>
    <path d="M0,330 L0,310 C250,318 500,272 700,240 C850,232 1000,228 1200,262 L1200,330Z" fill="var(--soft)"/>
  </svg>
  <div class="sec-title" style="left:484px;top:358px">
    <svg class="flower-icon" viewBox="0 0 32 32"><g fill="var(--orange)"><circle cx="16" cy="6" r="5.5"/><circle cx="16" cy="26" r="5.5"/><circle cx="6" cy="16" r="5.5"/><circle cx="26" cy="16" r="5.5"/><circle cx="9" cy="9" r="4.5"/><circle cx="23" cy="23" r="4.5"/><circle cx="23" cy="9" r="4.5"/><circle cx="9" cy="23" r="4.5"/></g><circle cx="16" cy="16" r="4" fill="var(--soft)"/></svg>
    <span class="script">Contact</span><span>Us</span>
  </div>
  <p>Lorem ipsum dolor sit amet, consectetur adipiscing elit, sed do eiusmod tempor incididunt ut labore et dolore magna aliqua.</p>
  <div class="btn green" style="left:270px;top:521px;width:283px;height:42px;font-size:14px">New Florist Franchise Inquiry</div>
  <div class="btn" style="left:570px;top:518px;width:360px;height:42px;font-size:14px">Professional Florist Franchise Inquiry</div>
</section>

<footer class="site-footer">
  <div class="brand" style="left:125px;top:80px;font-size:28px"><span class="dot"></span>Lantern Petals</div>
  <h4 style="left:110px;top:168px">Follow us</h4>
  <div class="abs" style="left:390px;top:72px;width:1px;height:175px;background:var(--footer-line)"></div>
  <h4 style="left:432px;top:70px">Quick Links</h4>
  <ul class="links" style="left:432px;top:104px"><li>Home</li><li>About</li><li>For Supermarkets</li><li>For Franchisees</li><li>Contact</li></ul>
  <h4 style="left:640px;top:70px">Our Company</h4>
  <ul class="links" style="left:640px;top:104px"><li>Terms &amp; Conditions</li><li>Privacy Policy</li><li>About Us</li><li>Support</li></ul>
  <h4 style="left:864px;top:70px">Contact us</h4>
  <div class="abs" style="left:0;top:272px;width:1200px;height:1px;background:var(--footer-line)"></div>
  <div class="copyright">©Copyrights 2024 Lantern-Petals &nbsp;&nbsp;| &nbsp;&nbsp;All Rights Reserved</div>
</footer>
<div class="social"><span></span><span></span><span></span><span></span></div>
<div class="contact-list" style="color:var(--white)">
  <div><svg width="12" height="17" viewBox="0 0 12 17"><path d="M6 0a6 6 0 0 1 6 6c0 4-6 11-6 11S0 10 0 6a6 6 0 0 1 6-6z" fill="#fff"/><circle cx="6" cy="6" r="2.2" fill="var(--footer)"/></svg><span>Lorem ipsum dolor sit<br>amet, consectetur adipiscing</span></div>
  <div><svg width="15" height="15" viewBox="0 0 15 15"><path d="M3 0l3 3.5-1.8 2.2a9 9 0 0 0 5 5l2.2-1.8L15 12l-2 3C6 15 0 9 0 2z" fill="#fff"/></svg><span>+1.555.014.2278</span></div>
  <div><svg width="15" height="12" viewBox="0 0 15 12"><rect width="15" height="12" rx="1" fill="#fff"/><path d="M0 1l7.5 6L15 1" fill="none" stroke="var(--footer)" stroke-width="1.5"/></svg><span>hello@lanternpetals.example</span></div>
</div>

</body>
</html>
```